Retractable banner.
Health Check For Pets
Check for Ear Mites
Skin Health
Fleas & Ticks

A space SERVE BY <NAME OF CLINIC>

Ideally contain pictures of cats and dogs

```html
<!DOCTYPE html>
<html lang="en">
<head>
<meta charset="utf-8">
<title>Health Check For Pets – Retractable Banner</title>
<link href="https://fonts.googleapis.com/css2?family=Montserrat:wght@500;600;700;800;900&display=swap" rel="stylesheet">
<style>
  :root {
    --page-bg: #e6e7e9;
    --banner-bg: #fbfbf9;
    --brand-red: #c8161d;
    --ink-dark: #2b2b2b;
    --ink-shadow: #3a0a0c;
    --icon-ring: #1f1f1f;
    --mite-tone: #ecd77f;
    --dog-tone: #8fb7e4;
    --flea-tone: #7a3a1c;
    --cat-tone-a: #8a7a66;
    --cat-tone-b: #4b3f33;
    --dog-photo-a: #d49a4c;
    --dog-photo-b: #a86a2a;
  }
  * { box-sizing: border-box; margin: 0; padding: 0; }
  html, body { width: 1200px; height: 825px; overflow: hidden; }
  body {
    background: var(--page-bg);
    font-family: "Montserrat", sans-serif;
    display: flex; align-items: center; justify-content: center;
  }
  .banner {
    position: relative;
    width: 1120px; height: 745px;
    background: var(--banner-bg);
    box-shadow: 0 4px 18px rgba(0,0,0,.12);
    overflow: hidden;
  }
  .photo { position: absolute; border-radius: 40px; }
  .photo--cat {
    left: 40px; top: 250px; width: 150px; height: 470px;
    background: linear-gradient(160deg, var(--cat-tone-a), var(--cat-tone-b));
    border-radius: 60px 60px 30px 30px;
  }
  .photo--dog {
    left: 760px; top: 40px; width: 320px; height: 600px;
    background: linear-gradient(160deg, var(--dog-photo-a), var(--dog-photo-b));
    border-radius: 120px 140px 40px 40px;
  }
  .headline {
    position: absolute; left: 200px; top: 60px; width: 560px;
    text-align: center;
    color: var(--brand-red);
    font-weight: 900;
    font-size: 78px; line-height: 1;
    letter-spacing: 1px;
    text-shadow: 3px 3px 0 var(--ink-shadow);
  }
  .headline__line { display: block; }
  .headline__line + .headline__line { margin-top: 8px; }
  .headline__tick {
    position: absolute; right: -36px; top: -22px; width: 70px; height: 60px;
  }
  .concerns {
    position: absolute; left: 210px; top: 290px; width: 540px;
    display: flex; justify-content: space-between;
  }
  .concern { width: 170px; text-align: center; }
  .concern__icon {
    width: 130px; height: 130px; margin: 0 auto;
    border-radius: 50%;
    border: 5px solid var(--icon-ring);
    background: #fff;
    display: flex; align-items: center; justify-content: center;
  }
  .concern__art { width: 78px; height: 78px; border-radius: 40%; }
  .concern__art--mite { background: var(--mite-tone); }
  .concern__art--dog { background: var(--dog-tone); }
  .concern__art--flea { background: var(--flea-tone); }
  .concern__label {
    margin-top: 16px;
    color: var(--brand-red);
    font-weight: 800; font-size: 30px; line-height: 1.05;
    text-shadow: 1px 1px 0 var(--ink-shadow);
  }
  .credit {
    position: absolute; left: 230px; top: 580px; width: 520px;
    text-align: center; color: var(--ink-dark);
  }
  .credit__rule { height: 3px; background: var(--ink-dark); }
  .credit__lead {
    display: inline-block;
    margin-top: -14px; padding: 0 14px;
    background: var(--banner-bg);
    font-weight: 700; font-size: 20px; letter-spacing: 1px;
    position: relative; top: -12px;
  }
  .credit__name { font-weight: 800; font-size: 40px; margin-top: -2px; }
  .credit__name-accent { font-size: 46px; letter-spacing: 1px; }
</style>
</head>
<body>
  <main class="banner">
    <div class="photo photo--cat" role="img" aria-label="Photo of a tabby cat standing and looking up"></div>
    <div class="photo photo--dog" role="img" aria-label="Photo of a tan dog standing and looking to the left"></div>

    <h1 class="headline">
      <span class="headline__line" style="position:relative;">HEALTH CHECK
        <svg class="headline__tick" viewBox="0 0 70 60" aria-hidden="true">
          <path d="M6 34 L24 52 L66 6" fill="none" stroke="var(--ink-dark)" stroke-width="9" stroke-linecap="round" stroke-linejoin="round"/>
        </svg>
      </span>
      <span class="headline__line">FOR PETS</span>
    </h1>

    <section class="concerns">
      <div class="concern">
        <div class="concern__icon"><div class="concern__art concern__art--mite" role="img" aria-label="Illustration of an ear mite"></div></div>
        <p class="concern__label">EAR<br>MITES</p>
      </div>
      <div class="concern">
        <div class="concern__icon"><div class="concern__art concern__art--dog" role="img" aria-label="Illustration of a sitting dog"></div></div>
        <p class="concern__label">SKIN<br>HEALTH</p>
      </div>
      <div class="concern">
        <div class="concern__icon"><div class="concern__art concern__art--flea" role="img" aria-label="Illustration of a flea"></div></div>
        <p class="concern__label">FLEAS<br>&amp; TICKS</p>
      </div>
    </section>

    <footer class="credit">
      <div class="credit__rule"></div>
      <span class="credit__lead">SERVE BY:</span>
      <p class="credit__name">Pet Health Care <span class="credit__name-accent">CLINIC</span></p>
    </footer>
  </main>
</body>
</html>
```